Stylish business cards for KV7

To create an appealing and professional business card design for a WOMEN Owned Construction Supply Company.
2 sided card. Incorporate brand elements, curvy, colorful, sleek and bright. No solid white background. attached samples of styles added shapes/ribbons. Want something with that WOW that looks awesome, factor. It is a new logo, so feel free to mess with logo colors in the blue and teal factors that can look good with both dark and light background. If you want to try a watermark with just the KV7, without the "Supply" that might look cool to.

Industry/Entity Type

Women owned construction supply company

Contact Information for Business Card

Name, Title, and phone number and email, web page. maybe spot for qr code.

Font styles to use
Sans Serif

Requirements
Nice to have
• would love to see colors, maybe stylish ribbon dividers or some sort of 2 or 3 tone color card that compliments logo.
Should not have
• Please do not have all white background. Do not include Home/reale state/ or building images.

```html
<!DOCTYPE html>
<html lang="en">
<head>
<meta charset="UTF-8">
<title>KV7 Supply – Business Card</title>
<link href="https://fonts.googleapis.com/css2?family=Montserrat:wght@400;600;700&display=swap" rel="stylesheet">
<style>
  :root {
    --page-bg: #1d1d1f;
    --card-white: #f3f3f3;
    --navy: #1b3859;
    --navy-deep: #1a3658;
    --teal: #2191b6;
    --white: #ffffff;
    --watermark: rgba(255, 255, 255, 0.055);
  }
  * { margin: 0; padding: 0; box-sizing: border-box; }
  html, body {
    width: 1200px;
    height: 1059px;
    overflow: hidden;
    background: var(--page-bg);
    font-family: "Montserrat", sans-serif;
  }
  .card {
    position: absolute;
    border-radius: 18px;
    overflow: hidden;
  }
  /* Front */
  .card--front {
    left: 256px; top: 89px;
    width: 688px; height: 390px;
    background: var(--card-white);
  }
  .brand {
    position: absolute;
    left: 0; right: 0;
    display: flex;
    align-items: center;
    justify-content: center;
    gap: 14px;
    font-weight: 700;
    letter-spacing: 0.5px;
  }
  .brand__dot {
    width: 16px; height: 16px;
    border-radius: 50%;
    background: var(--teal);
  }
  .card--front .brand {
    top: 78px;
    font-size: 52px;
    color: var(--navy);
  }
  .info-band {
    position: absolute;
    left: 0; top: 220px;
    width: 100%; height: 137px;
    display: flex;
  }
  .info-band__person {
    width: 344px;
    background: var(--navy);
    color: var(--white);
    padding: 45px 0 0 28px;
  }
  .person__name {
    font-weight: 700;
    font-size: 22px;
    color: var(--teal);
    letter-spacing: 0.3px;
    line-height: 1;
  }
  .person__title {
    font-size: 16px;
    margin-top: 4px;
  }
  .info-band__contact {
    flex: 1;
    background: var(--teal);
    color: var(--white);
    padding: 9px 0 0 24px;
    font-size: 14.5px;
    line-height: 1.35;
  }
  .contact__address { margin-bottom: 9px; }
  .contact__row {
    display: flex;
    align-items: center;
    gap: 8px;
    height: 25px;
  }
  .contact__icon { width: 13px; height: 13px; flex: none; }
  /* Back */
  .card--back {
    left: 254px; top: 547px;
    width: 693px; height: 393px;
    background: var(--navy-deep);
  }
  .card--back .watermark {
    position: absolute;
    left: 10px; top: 70px;
    font-weight: 700;
    font-size: 260px;
    line-height: 1;
    color: var(--watermark);
    letter-spacing: -4px;
  }
  .card--back .brand {
    top: 160px;
    font-size: 60px;
    color: var(--white);
  }
</style>
</head>
<body>
  <section class="card card--front" aria-label="Business card front">
    <div class="brand"><span class="brand__name">KV7 Supply</span><span class="brand__dot"></span></div>
    <div class="info-band">
      <div class="info-band__person">
        <p class="person__name">DANA WHITFIELD</p>
        <p class="person__title">CEO/Founder</p>
      </div>
      <div class="info-band__contact">
        <p class="contact__address">P.O Box 4170 Harbour Lane<br>Eastfield QL 40210</p>
        <p class="contact__row">
          <svg class="contact__icon" viewBox="0 0 24 24" fill="#fff"><path d="M6.6 10.8a15.1 15.1 0 0 0 6.6 6.6l2.2-2.2a1 1 0 0 1 1-.25 11.4 11.4 0 0 0 3.6.57 1 1 0 0 1 1 1V20a1 1 0 0 1-1 1A17 17 0 0 1 3 4a1 1 0 0 1 1-1h3.5a1 1 0 0 1 1 1c0 1.25.2 2.45.57 3.57a1 1 0 0 1-.25 1z"/></svg>
          555.014.0288
        </p>
        <p class="contact__row">
          <svg class="contact__icon" viewBox="0 0 24 24" fill="none" stroke="#fff" stroke-width="2"><rect x="2" y="5" width="20" height="14"/><path d="M2 5l10 8 10-8M2 19l7-7M22 19l-7-7"/></svg>
          info@kv7supply.com.au
        </p>
        <p class="contact__row">
          <svg class="contact__icon" viewBox="0 0 24 24" fill="none" stroke="#fff" stroke-width="1.8"><circle cx="12" cy="12" r="10"/><ellipse cx="12" cy="12" rx="4.5" ry="10"/><path d="M2 12h20M4 7h16M4 17h16"/></svg>
          www.kv7supply.com.au
        </p>
      </div>
    </div>
  </section>

  <section class="card card--back" aria-label="Business card back">
    <div class="watermark" aria-hidden="true">KV7</div>
    <div class="brand"><span class="brand__name">KV7 Supply</span><span class="brand__dot"></span></div>
  </section>
</body>
</html>
```